HARBORLINE AUTO GLASS

Mobile Glass Shop:

1) Windshield REPAIR 2)Windshield replacment 3) Rear Windshield Replacment 4) Side Window Replacment 5) car window replacment 6) Power Window Repair.

Schedual a service within 24 hour with one of our certified technicians.
Updates

See "brightvane auto repair" web site for referance on the nature of our buisness and service. www.brightvane-example.com

Coding

```html
<!DOCTYPE html>
<html lang="en">
<head>
<meta charset="utf-8">
<title>Harborline Auto Glass</title>
<link rel="stylesheet" href="https://fonts.googleapis.com/css2?family=Anton&family=Raleway:wght@400;500;600;700&display=swap">
<style>
:root{
  --navy:#1a5c98;
  --blue:#2a75b6;
  --sky:#5ba6da;
  --pale:#e6f1fa;
  --ink:#1e1e1e;
  --text:#3b3b3b;
  --dark:#2b2b2b;
  --white:#ffffff;
  --star:#f4b63a;
}
*{box-sizing:border-box;margin:0;padding:0}
html,body{width:1200px;height:3195px;overflow:hidden;background:var(--white)}
body{position:relative;font-family:"Raleway",sans-serif;color:var(--text)}
.abs{position:absolute}
a{color:inherit;text-decoration:none}

/* header */
.brand{left:114px;top:24px;display:flex;align-items:center;gap:10px}
.brand-mark{width:38px;height:38px;background:var(--blue)}
.brand-name{font-family:"Raleway",sans-serif;font-weight:700;color:var(--navy);font-size:17px;line-height:19px;letter-spacing:.5px}
.nav{left:470px;top:42px;display:flex;gap:28px;font-size:15px;font-weight:500;color:#333}
.nav .active{color:var(--blue)}
.btn{display:flex;align-items:center;justify-content:center;color:var(--white);font-weight:600;font-size:15px;border-radius:5px;background:linear-gradient(180deg,var(--blue),var(--navy))}
.book{left:941px;top:29px;width:147px;height:48px}

/* hero */
.hero{left:0;top:97px;width:1200px;height:595px}
.hero-text{right:110px;top:248px;text-align:right;color:var(--white)}
.hero-kicker{font-family:"Anton",sans-serif;font-size:24px;text-align:left}
.hero-title{font-family:"Anton",sans-serif;font-size:92px;line-height:1.1;margin-top:4px}
.hero-sub{font-size:40px;letter-spacing:9px;font-weight:500;margin-top:-4px}
.hero-btn{left:793px;top:479px;width:149px;height:48px}

/* sections */
.section-title{left:0;width:1200px;text-align:center;font-family:"Anton",sans-serif;font-size:46px;color:var(--navy);letter-spacing:.5px}
.section-title span{color:var(--sky)}
.card{width:275px;height:297px;background:var(--white);box-shadow:0 4px 18px rgba(0,0,0,.09);text-align:center}
.card svg{margin-top:44px}
.card h3{font-size:17px;font-weight:600;color:var(--ink);margin-top:14px}
.card p{font-size:14px;line-height:30px;margin:8px 28px 0}
.card .more{position:absolute;left:0;bottom:0;width:100%;height:44px;border-top:1px solid #e4e4e4;display:flex;align-items:center;justify-content:center;color:var(--blue);font-weight:600;font-size:14px}
.card .more.on{background:var(--sky);color:var(--white);border-top:none;left:-2px;width:279px}

/* about */
.about{left:0;top:1610px;width:1200px;height:560px}
.about-title{top:1712px;color:var(--white)}
.about-copy{left:110px;width:980px;top:1811px;text-align:center;color:var(--white);font-size:15px;line-height:30px}
.about-copy p+p{margin-top:13px;font-weight:500}
.about-copy p:first-child{font-weight:600}
.about-btn{left:528px;top:2034px;width:148px;height:49px}

/* testimonials */
.review{width:468px;height:271px;background:var(--white);box-shadow:0 4px 18px rgba(0,0,0,.09)}
.review .avatar{position:absolute;left:22px;top:30px;width:102px;height:102px;border-radius:50%;background:linear-gradient(160deg,#c9a789,#6b5646)}
.review .quote{position:absolute;left:34px;top:128px;font-family:Georgia,serif;font-size:120px;line-height:1;color:#b9d3ea}
.review .who{position:absolute;left:150px;top:36px;right:30px}
.review h4{font-size:17px;font-weight:500;color:var(--ink)}
.review .meta{display:flex;align-items:center;gap:18px;margin-top:8px;font-size:9px;color:#777}
.review .meta i{display:inline-block;width:13px;height:13px;border-radius:50%;background:#8a8a8a;margin-right:4px;vertical-align:middle}
.stars{color:var(--star);font-size:16px;letter-spacing:1px}
.review p{font-size:14px;line-height:30px;margin-top:12px;color:#444}
.review p b{color:var(--blue)}
.review .tab{position:absolute;right:0;bottom:0;width:22px;height:18px;background:#b9d6ef}
.view-btn{left:548px;top:2699px;width:108px;height:48px}

/* footer */
.footer{left:0;top:2800px;width:1200px;height:395px}
.foot-brand{left:112px;top:2920px;display:flex;align-items:center;gap:18px}
.foot-brand .brand-mark{width:70px;height:70px;background:var(--blue)}
.foot-brand .brand-name{font-size:34px;line-height:40px;color:var(--sky);letter-spacing:2px}
.foot-col{color:var(--white);font-size:16px}
.foot-col h5{font-size:16px;font-weight:600;letter-spacing:.3px;margin-bottom:10px}
.foot-col li{list-style:none;line-height:30px}
.contact li{display:flex;gap:8px;line-height:30px;margin-bottom:12px}
.contact svg{flex:none;margin-top:8px}
.copy{left:0;width:1200px;top:3130px;text-align:center;color:var(--white);font-size:15px}
</style>
</head>
<body>

<!-- header -->
<div class="abs brand">
  <div class="brand-mark"></div>
  <div class="brand-name">HARBORLINE<br>AUTO GLASS</div>
</div>
<nav class="abs nav">
  <a class="active">Home</a><a>About</a><a>Services</a><a>My Appointment</a><a>Contact</a>
</nav>
<a class="abs btn book">BOOK NOW</a>

<!-- hero -->
<svg class="abs hero" viewBox="0 0 1200 595" role="img" aria-label="Technician fitting a new windshield onto a car with suction cups">
  <defs>
    <linearGradient id="heroFill" x1="0" y1="0" x2="1" y2="0">
      <stop offset="0" stop-color="#4a4f58"/>
      <stop offset=".35" stop-color="#6d86a3"/>
      <stop offset=".6" stop-color="#2f6aa3"/>
      <stop offset="1" stop-color="#1c5b98"/>
    </linearGradient>
  </defs>
  <path d="M0 0 Q600 40 1200 0 L1200 565 Q600 590 0 555 Z" fill="url(#heroFill)"/>
  <path d="M0 555 Q600 590 1200 565 L1200 572 Q600 598 0 562 Z" fill="#d9e7f3"/>
</svg>
<div class="abs hero-text">
  <div class="hero-kicker">WELCOME TO</div>
  <div class="hero-title">HARBORLINE</div>
  <div class="hero-sub">AUTO GLASS</div>
</div>
<a class="abs btn hero-btn">LEARN MORE</a>

<!-- services -->
<h2 class="abs section-title" style="top:762px">OUR <span>SERVICES</span></h2>

<div class="abs card" style="left:114px;top:877px">
  <svg width="74" height="46" viewBox="0 0 74 46" fill="none" stroke="#1a2f4a" stroke-width="3"><path d="M8 6 Q37 0 66 6 L72 40 Q37 34 2 40 Z"/><path d="M30 18 L36 28 L44 20" stroke="var(--blue)"/><rect x="58" y="24" width="14" height="18" fill="#a9cdeb" stroke="none"/></svg>
  <h3>Windshield Repair</h3>
  <p>Lorem ipsum dolor sit amet, consecetur adipiscing, sed do eiusmod tempor incid.</p>
  <a class="more">More</a>
</div>
<div class="abs card" style="left:464px;top:877px">
  <svg width="74" height="60" viewBox="0 0 74 60" fill="none" stroke="#1a2f4a" stroke-width="2.5"><path d="M4 2 L36 4 L32 20 L8 20 Z"/><path d="M24 32 L56 32 L62 44 L62 56 L18 56 L18 44 Z"/><rect x="58" y="36" width="14" height="22" fill="#a9cdeb" stroke="none"/></svg>
  <h3>Windshield replacment</h3>
  <p>Lorem ipsum dolor sit amet, consecetur adipiscing, sed do eiusmod tempor incid.</p>
  <a class="more on">More</a>
</div>
<div class="abs card" style="left:813px;top:877px">
  <svg width="74" height="50" viewBox="0 0 74 50" fill="none" stroke="#1a2f4a" stroke-width="3"><path d="M4 14 Q30 0 62 8 L60 44 Q30 34 10 44 Z"/><path d="M14 20 L18 14 M20 22 L24 16" stroke="var(--blue)"/><rect x="58" y="22" width="12" height="24" fill="#a9cdeb" stroke="none"/></svg>
  <h3>Rear Windshield Replacment</h3>
  <p>Lorem ipsum dolor sit amet, consecetur adipiscing, sed do eiusmod tempor incid.</p>
  <a class="more">More</a>
</div>
<div class="abs card" style="left:114px;top:1219px">
  <svg width="60" height="52" viewBox="0 0 60 52" fill="none" stroke="#1a2f4a" stroke-width="2.5"><path d="M6 2 L26 2 L40 18 L40 50 L6 50 Z"/><path d="M10 6 L24 6 L34 18 L10 18 Z" stroke="var(--blue)"/><rect x="40" y="26" width="16" height="24" fill="#a9cdeb" stroke="none"/></svg>
  <h3>Side Window Replacment</h3>
  <p>Lorem ipsum dolor sit amet, consecetur adipiscing, sed do eiusmod tempor incid.</p>
  <a class="more">More</a>
</div>
<div class="abs card" style="left:464px;top:1219px">
  <svg width="74" height="50" viewBox="0 0 74 50" fill="none" stroke="#1a2f4a" stroke-width="3"><path d="M16 4 L50 4 L58 20 L58 44 L8 44 L8 20 Z"/><path d="M8 20 L58 20"/><path d="M16 30 L28 30 M38 30 L50 30 M24 38 L42 38"/><rect x="58" y="24" width="14" height="22" fill="#a9cdeb" stroke="none"/></svg>
  <h3>car window replacment</h3>
  <p>Lorem ipsum dolor sit amet, consecetur adipiscing, sed do eiusmod tempor incid.</p>
  <a class="more">More</a>
</div>
<div class="abs card" style="left:813px;top:1219px">
  <svg width="74" height="50" viewBox="0 0 74 50" fill="none" stroke="#1a2f4a" stroke-width="2.5"><path d="M6 6 Q36 0 66 6 L64 42 Q36 36 4 42 Z"/><path d="M36 10 L36 34 M24 22 L48 22 M28 14 L44 30 M44 14 L28 30" stroke="var(--blue)" stroke-width="2"/><rect x="60" y="26" width="12" height="20" fill="#a9cdeb" stroke="none"/></svg>
  <h3>Power Window Repair</h3>
  <p>Lorem ipsum dolor sit amet, consecetur adipiscing, sed do eiusmod tempor incid.</p>
  <a class="more">More</a>
</div>

<!-- about -->
<svg class="abs about" viewBox="0 0 1200 560" role="img" aria-label="Blue band with a cracked glass texture">
  <path d="M0 8 Q600 -10 1200 8 L1200 522 Q600 575 0 522 Z" fill="var(--sky)"/>
</svg>
<h2 class="abs section-title about-title">ABOUT US</h2>
<div class="abs about-copy">
  <p>Lorem ipsum dolor sit amet, consectetur adipiscing elit, sed do eiusmod tempor incididunt ut labore et dolore magna aliqua. Ut enim ad minim veniam, quis nostrud exercitation ullamco laboris nisi ut aliquip ex ea commodo consequat.</p>
  <p>Lorem ipsum dolor sit amet, consectetur adipiscing elit, sed do eiusmod tempor incididunt ut labore et dolore magna aliqua. Ut enim ad minim veniam, quis nostrud exercitation ullamco laboris nisi ut aliquip ex ea commodo consequat. Duis aute irure dolor in reprehenderit in voluptate velit esse cillum dolore eu fugiat nulla pariatur. Excepteur sint occaecat cupidatat non proident, sunt in culpa qui officia deserunt mollit anim id est laborum</p>
</div>
<a class="abs btn about-btn">LEARN MORE</a>

<!-- testimonials -->
<h2 class="abs section-title" style="top:2242px">CLIENT <span>TESTIMONIALS</span></h2>

<div class="abs review" style="left:112px;top:2373px">
  <div class="avatar" role="img" aria-label="Portrait of the reviewer"></div>
  <div class="quote">&ldquo;</div>
  <div class="who">
    <h4>Dale Morrow</h4>
    <div class="meta"><span><i></i>Verified review</span><span class="stars">★★★★★</span></div>
    <p>Lorem ipsum dolor sit amet, consadipiscing elit, sed do eiusmod bjku tempor incididunt ut labor veniam, quis nostrud exen ullamco labo cvds nisi ut aliquip ex ea comequmat. aute irure dolor in reprehendr. <b>»</b></p>
  </div>
  <div class="tab"></div>
</div>
<div class="abs review" style="left:620px;top:2373px">
  <div class="avatar" role="img" aria-label="Portrait of the reviewer" style="background:linear-gradient(160deg,#b88a6c,#2c3550)"></div>
  <div class="quote">&ldquo;</div>
  <div class="who">
    <h4>Nina Castell</h4>
    <div class="meta"><span><i></i>Verified review</span><span class="stars">★★★★★</span></div>
    <p>Lorem ipsum dolor sit amet, consadipiscing elit, sed do eiusmod bjku tempor incididunt ut labor veniam, quis nostrud exen ullamco labo cvds nisi ut aliquip ex ea comequmat. aute irure dolor in reprehendr. <b>»</b></p>
  </div>
  <div class="tab"></div>
</div>
<a class="abs btn view-btn">View All</a>

<!-- footer -->
<svg class="abs footer" viewBox="0 0 1200 395" role="img" aria-label="Dark footer with a cracked glass texture">
  <path d="M0 14 Q600 40 1200 0 L1200 395 L0 395 Z" fill="var(--dark)"/>
</svg>
<div class="abs foot-brand">
  <div class="brand-mark"></div>
  <div class="brand-name">HARBORLINE<br>AUTO GLASS</div>
</div>
<div class="abs foot-col" style="left:569px;top:2898px">
  <h5>QUICK LINKS</h5>
  <ul><li>Home</li><li>About</li><li>Services</li><li>My Appointment</li><li>Contact</li></ul>
</div>
<div class="abs foot-col contact" style="left:862px;top:2898px">
  <h5>CONTACT</h5>
  <ul>
    <li><svg width="10" height="14" viewBox="0 0 10 14"><path d="M5 0a5 5 0 0 1 5 5c0 4-5 9-5 9S0 9 0 5a5 5 0 0 1 5-5z" fill="#fff"/><circle cx="5" cy="5" r="2" fill="#2b2b2b"/></svg><span>Harborline auto glass,<br>Address Comes Here</span></li>
    <li><svg width="13" height="13" viewBox="0 0 13 13"><path d="M2 0l3 3-2 2c1 2 3 4 5 5l2-2 3 3-2 2C5 13 0 8 0 2z" fill="#fff"/></svg><span>+1 555-010-0142</span></li>
    <li><svg width="14" height="11" viewBox="0 0 14 11"><rect width="14" height="11" rx="1" fill="#fff"/><path d="M0 1l7 5 7-5" stroke="#2b2b2b" fill="none"/></svg><span>info@harborlineautoglass.example</span></li>
  </ul>
</div>
<div class="abs copy">2022 Harborline Auto Glass. All Rights Reserved.</div>

</body>
</html>
```